Pitch Orchard

We need a logo and website that reflects a platform, enabling for users (consultants and corporate clients) to have for them powerpoint slides produced.
See the mockup in attachment - Look& feel Style www.brintova.com. See a similar website content (but outdated presentation and to be made more appealing with new modern ways to promote (old website with same proposition: http://www.yondercraftpanel.com/). Look and feel wished: www.glantirex.com (see number that show dynamic evolution) or www.brintova.com

We have no name - that is part of the mission

```html
<!DOCTYPE html>
<html lang="en">
<head>
<meta charset="utf-8">
<title>Northlane Visual</title>
<link rel="stylesheet" href="https://fonts.googleapis.com/css2?family=Lato:wght@300;400;700&family=Raleway:wght@300;400;600&display=swap">
<style>
:root{
  --yellow:#e3c92a;
  --orange:#e89a0f;
  --orange-bg:#e5a11e;
  --ink:#222;
  --grey-text:#666;
  --light:#f1f1f1;
  --dark:#1d1d1d;
  --footer:#3b3b3b;
  --footer-bottom:#2a2a2a;
  --white:#fff;
}
*{box-sizing:border-box;margin:0;padding:0}
html,body{width:1200px;height:3750px;overflow:hidden}
body{position:relative;font-family:"Lato",sans-serif;color:var(--ink);background:var(--white)}
.abs{position:absolute}

/* header / hero */
.hero{left:0;top:0;width:1200px;height:658px;background:linear-gradient(160deg,#5a4a3a 0%,#c9c3b8 35%,#8f7f6c 60%,#2f2620 100%)}
.brand{left:95px;top:20px;display:flex;align-items:center;gap:12px}
.brand-dot{width:34px;height:34px;border-radius:50%;background:var(--orange)}
.brand-name{font-family:"Lato",sans-serif;font-weight:700;font-size:26px;color:var(--white)}
.brand-tag{left:143px;top:54px;font-size:13px;color:var(--yellow);font-style:italic}
.nav{right:100px;top:36px;display:flex;gap:26px;font-size:15px;color:var(--white)}
.hero-title{left:250px;top:392px;width:700px;text-align:center;font-family:"Raleway",sans-serif;font-weight:600;font-size:44px;line-height:50px;color:var(--white)}
.btn-try{left:505px;top:555px;width:170px;height:53px;background:#1e1e1e;color:var(--white);font-weight:700;font-size:20px;display:flex;align-items:center;justify-content:center;letter-spacing:1px}

/* stats */
.stats{left:0;top:658px;width:1200px;height:222px;background:var(--yellow)}
.stat{width:220px;text-align:center}
.stat svg{display:block;margin:0 auto}
.stat-num{position:absolute;left:0;top:40px;width:220px;font-size:27px}
.stat-label{margin-top:8px;font-size:17px;line-height:20px}

/* clients */
.clients{left:0;top:880px;width:1200px;height:285px;background:var(--light)}
.client-row{left:95px;top:80px;width:1010px;display:flex;justify-content:space-between;align-items:center;font-size:28px;color:#8a8a8a;font-weight:700}
.client-ring{display:inline-block;width:14px;height:14px;border-radius:50%;background:#9a9a9a;margin-right:6px;vertical-align:middle}
.arrow{font-size:34px;color:#777;font-weight:300}
.social{display:flex;gap:28px}
.social span{width:34px;height:34px;border:2px solid #333;display:flex;align-items:center;justify-content:center;font-size:10px;font-weight:700;color:#333}

/* value */
.section-title{width:1200px;left:0;text-align:center;font-family:"Raleway",sans-serif;font-weight:300;font-size:46px;color:#222}
.rule{width:84px;height:3px;background:var(--orange);left:558px}
.value-text{left:108px;top:1322px;width:984px;font-size:12.5px;line-height:22px;color:var(--grey-text)}
.value-text p{margin-bottom:14px}
.card{width:362px;height:148px;background:var(--light);text-align:center;padding:26px 28px}
.card h3{font-family:"Raleway",sans-serif;font-weight:400;font-size:20px;margin-bottom:10px}
.card p{font-size:12.5px;line-height:21px;color:var(--grey-text)}

/* before / after */
.compare{left:0;top:1738px;width:1200px;height:400px;background:var(--dark)}
.tag{width:138px;height:38px;background:var(--yellow);font-size:18px;display:flex;align-items:center;justify-content:center}
.sketch{width:295px;height:213px;background:linear-gradient(180deg,#fafafa,#e6e6e6);border:3px solid #ccc}
.slide-arrow{width:22px;height:22px;background:#555;color:#ddd;font-size:13px;display:flex;align-items:center;justify-content:center}

/* gallery */
.filters{left:225px;top:2292px;display:flex;gap:8px}
.filters span{height:30px;padding:0 14px;border:1px solid #ddd;font-size:13px;display:flex;align-items:center}
.filters .on{background:var(--yellow);border-color:var(--yellow)}
.thumb{width:394px;height:155px;border:6px solid #eee;background:linear-gradient(90deg,#e7f0f8,#ffffff 50%,#d5e9f4)}

/* contact */
.contact{left:0;top:2788px;width:1200px;height:675px;background:linear-gradient(120deg,#e9a523,#df961a 60%,#eaa929)}
.form{left:143px;top:2843px;width:932px;height:570px;background:var(--white)}
.field{width:388px;height:40px;border:1px solid #ccc;font-size:13px;color:#999;padding:11px 12px}
.field.tall{height:122px}
.browse{right:0;top:0;width:72px;height:38px;background:var(--yellow);color:#333;font-size:13px;font-weight:700;display:flex;align-items:center;justify-content:center}
.btn{width:83px;height:33px;background:var(--orange);color:var(--white);font-size:13px;font-weight:700;display:flex;align-items:center;justify-content:center}

/* footer */
.footer{left:0;top:3463px;width:1200px;height:225px;background:var(--footer);color:#cfcfcf}
.fcol{top:40px;width:240px;font-size:11.5px;line-height:15px}
.fcol h4{font-size:15px;font-weight:400;color:var(--white);margin-bottom:18px}
.footer-bottom{left:0;top:3688px;width:1200px;height:62px;background:var(--footer-bottom)}
.footer-bottom .social{position:absolute;left:100px;top:17px;gap:6px}
.footer-bottom .social span{width:24px;height:24px;border:1px solid #ddd;color:#ddd;font-size:7px}
.copy{right:95px;top:24px;font-size:11px;color:#ddd}
</style>
</head>
<body>

<div class="abs hero" role="img" aria-label="Photo of a presenter pointing at a bar chart in front of a seated business audience"></div>
<div class="abs brand"><span class="brand-dot"></span><span class="brand-name">Northlane Visual</span></div>
<div class="abs brand-tag">adds value to your presentation</div>
<nav class="abs nav"><span>Our value proposition</span><span>Who are we</span><span>Pricing</span><span>Contact</span><span>Our Gallery</span></nav>
<h1 class="abs hero-title">NLV is always preferred by clients across the world owing to the above factors</h1>
<div class="abs btn-try">TRY NOW !</div>

<section class="abs stats">
  <div class="abs stat" style="left:150px;top:27px"><svg width="118" height="118" viewBox="0 0 118 118"><circle cx="59" cy="59" r="54" fill="none" stroke="#222" stroke-width="3"/><path d="M59 5 A54 54 0 0 1 113 59" fill="none" stroke="#111" stroke-width="7"/></svg><div class="stat-num">12</div><div class="stat-label">Countries active</div></div>
  <div class="abs stat" style="left:362px;top:27px"><svg width="118" height="118" viewBox="0 0 118 118"><circle cx="59" cy="59" r="54" fill="none" stroke="#222" stroke-width="3"/><path d="M59 5 A54 54 0 0 1 113 59" fill="none" stroke="#111" stroke-width="7"/></svg><div class="stat-num">145</div><div class="stat-label">Corporate<br>Clients served</div></div>
  <div class="abs stat" style="left:590px;top:27px"><svg width="118" height="118" viewBox="0 0 118 118"><circle cx="59" cy="59" r="54" fill="none" stroke="#222" stroke-width="3"/><path d="M59 5 A54 54 0 0 1 113 59" fill="none" stroke="#111" stroke-width="7"/></svg><div class="stat-num">20,000</div><div class="stat-label">Slides<br>produced</div></div>
  <div class="abs stat" style="left:820px;top:27px"><svg width="118" height="118" viewBox="0 0 118 118"><circle cx="59" cy="59" r="54" fill="none" stroke="#222" stroke-width="3"/><path d="M59 5 A54 54 0 0 1 113 59" fill="none" stroke="#111" stroke-width="7"/></svg><div class="stat-num">1540</div><div class="stat-label">Free lance<br>consultants served</div></div>
</section>

<section class="abs clients">
  <div class="abs arrow" style="left:40px;top:85px">&lsaquo;</div>
  <div class="abs client-row"><span>Lumo</span><span>Verdan</span><span>Halcourt</span><span>Brava</span><span><i class="client-ring"></i>Quintel</span><span>Fernly</span><span>Osk Hale</span></div>
  <div class="abs arrow" style="left:1120px;top:85px">&rsaquo;</div>
  <div class="abs social" style="left:432px;top:205px"><span>Net</span><span>Chat</span><span>Pro</span><span>Pix</span><span>Web</span></div>
</section>

<h2 class="abs section-title" style="top:1208px">Our Value proposition</h2>
<div class="abs rule" style="top:1275px"></div>
<div class="abs value-text">
  <p>The main objective of Outsourcing PowerPoint service is to reduce the cost significantly without compromising quality. PITCH ORCHARD helps the customers to achieve this by providing high-quality presentations (management consulting golden standard, i.e. Harlow Grant, Denmore &amp; Co standard) at a fraction of the corporate or external consulting cost. Our sourcing presentation execution and design services to PITCH ORCHARD offers benefits not only in terms of cost reduction, but also in increased productivity and a guaranteed Quality Standard by former Management consultants from the leading Strategy houses (ex Denmore&amp;co).</p>
  <p>PITCH ORCHARD offers PowerPoint creative services in the following two categories:<br>1.Ad-hoc support<br>2.Dedicated support</p>
</div>
<div class="abs card" style="left:228px;top:1542px"><h3>Ad-hoc support</h3><p>Requests with quick turnaround time will be considered as Ad-hoc requests. Client can pre-book capacity with us for this sort of requests.</p></div>
<div class="abs card" style="left:640px;top:1542px"><h3>Dedicated support</h3><p>When extra service is required to prepare a workshop or an executive presentation for the next day, we will "upgrade" your ideas to a top management look&amp;feel standard.</p></div>

<section class="abs compare">
  <div class="abs tag" style="left:238px;top:57px">Before</div>
  <div class="abs tag" style="left:725px;top:57px">After</div>
  <div class="abs sketch" style="left:238px;top:124px" role="img" aria-label="Hand-drawn slide sketch before redesign"></div>
  <div class="abs sketch" style="left:675px;top:124px" role="img" aria-label="Hand-drawn slide sketch with structured layout after redesign"></div>
  <div class="abs slide-arrow" style="left:171px;top:226px">&#9664;</div>
  <div class="abs slide-arrow" style="left:1019px;top:226px">&#9654;</div>
</section>

<h2 class="abs section-title" style="top:2165px">Our Gallery</h2>
<div class="abs rule" style="top:2232px"></div>
<div class="abs filters"><span class="on">All</span><span>One-to-one production</span><span>High end production</span><span>Conversion</span><span>Visual enhancement</span><span>Illustration</span></div>
<div class="abs thumb" style="left:183px;top:2380px" role="img" aria-label="Sample slides with process diagrams"></div>
<div class="abs thumb" style="left:612px;top:2380px" role="img" aria-label="Sample slides showing a value proposition layout"></div>
<div class="abs thumb" style="left:183px;top:2555px" role="img" aria-label="Sample slides asking about expectations"></div>
<div class="abs thumb" style="left:612px;top:2555px" role="img" aria-label="Sample slides on professional development"></div>

<section class="abs contact" role="img" aria-label="Warm orange backdrop of a blurred office scene"></section>
<form class="abs form">
  <div class="abs field" style="left:52px;top:62px">Name</div>
  <div class="abs field" style="left:495px;top:62px">Phone No*</div>
  <div class="abs field" style="left:52px;top:125px">Organization</div>
  <div class="abs field" style="left:495px;top:125px">Fax No</div>
  <div class="abs field" style="left:52px;top:187px">Designation</div>
  <div class="abs field" style="left:495px;top:187px">Mobile No</div>
  <div class="abs field" style="left:52px;top:250px">Email ID *</div>
  <div class="abs field" style="left:495px;top:250px">Attach<span class="abs browse">Browse</span></div>
  <div class="abs field tall" style="left:52px;top:305px">Address</div>
  <div class="abs field tall" style="left:495px;top:305px">Comments</div>
  <div class="abs btn" style="left:377px;top:492px">SUBMIT</div>
  <div class="abs btn" style="left:477px;top:492px">RESET</div>
</form>

<footer class="abs footer">
  <div class="abs fcol" style="left:100px"><h4>About Us</h4>Northlane Visual Private Limited (NLV) is a PowerPoint presentation designing company based in India. We proud ourselves as a pioneer in presentation designing, to enable clients to outsource their powerpoint presentation in order to make it a professional quality presentation</div>
  <div class="abs fcol" style="left:375px"><h4>Services</h4>Presentation designing<br>Template Designing<br>Add-in creation<br>Posters/Banner/Brochure designing<br>Photo retouching and Enhancement<br>Excel programming<br>Data processing</div>
  <div class="abs fcol" style="left:633px"><h4>Contact Us</h4>Northlane Visual Private Limited,<br>18/4, Cedar Lane,<br>Riverside Park,<br>Chennai - 600 000,<br>India<br>hello@northlanevisual.com<br>studio@northlanevisual.com</div>
  <div class="abs fcol" style="left:933px;width:170px"><h4>Testimonials</h4>Excellent - thanks for extremely fast service. I really like the alternative suggestions as well and will have a hard time choosing the best from the best.<br>Thanks again.<br><br><b>Consultant - USA</b></div>
</footer>
<div class="abs footer-bottom">
  <div class="social"><span>Net</span><span>Chat</span><span>Pro</span><span>Pix</span><span>Web</span></div>
  <div class="abs copy">Copyright &copy; 2016. All rights reserved.</div>
</div>

</body>
</html>
```